Wordpress Design Project (Brookhollow)

We need a wordpress design for an established auction and real estate company based in New Hampshire. The winning design will incorporate the colors of logo (red and blue) creatively with black or gray in a very professional and clean layout. Client mentions liking the site http://www.pellandbids.example/ as a general idea.

Industry/Entity Type

Real Estate

Requirements
Must have
• Navigation:
1) Home (lorem text)
2) Upcoming Auctions
3) Auction Results
4) Sell or Consign
5) About Us
6) Services
7) FAQ
8) Contact Us

Site will have slideshow, initial image attached.
Sidebar widgets:
- Email sign up form
- Featured Auction (like at http://www.quillmarksales.example) - - - - Video Widget
- Testimonials widget

Footer will have smaller logo, contact info, and 2 association logos (attached)
-
Nice to have
• use of drop-down menu design for 'Services'
1) Appraisals
2) Consulting
Should not have
• please use no gavels in the design

```html
<!DOCTYPE html>
<html lang="en">
<head>
<meta charset="utf-8">
<title>Brookhollow Auctions</title>
<link href="https://fonts.googleapis.com/css2?family=Open+Sans:wght@400;600;700&family=Oswald:wght@400;500&display=swap" rel="stylesheet">
<style>
:root{
  --navy:#1c2f6b;
  --red:#c8201f;
  --dark:#2b2b2b;
  --bar:#3a3a3a;
  --grey:#e4e4e4;
  --text:#333;
  --muted:#777;
  --white:#fff;
}
*{box-sizing:border-box;margin:0;padding:0}
html,body{width:841px;height:1200px;overflow:hidden}
body{font-family:"Open Sans",Arial,sans-serif;color:var(--text);background:linear-gradient(#fff 0,#fff 380px,#d9d9d9 560px,#cfcfcf 1140px);position:relative;font-size:10px}
.header{height:58px;display:flex;align-items:center;padding-left:30px;gap:10px}
.brand-mark{width:34px;height:34px;border-radius:50%;background:var(--navy)}
.brand-name{font-family:"Oswald",sans-serif;font-size:22px;color:var(--navy);letter-spacing:2px;font-weight:500}
.nav{position:absolute;top:60px;left:25px;width:791px;height:22px;background:linear-gradient(#4a4a4a,#1e1e1e);display:flex;padding-left:10px}
.nav a{color:#fff;text-decoration:none;font-size:10px;padding:0 15px;line-height:22px}
.nav a.active{background:var(--navy)}
.slideshow{position:absolute;top:84px;left:25px;width:791px;height:305px;background:linear-gradient(135deg,#7a6f5e,#cfc7b6 35%,#8d8474 60%,#3f3a33);}
.slide-tab{position:absolute;top:0;right:30px;background:var(--red);color:#fff;font-size:8px;font-weight:700;padding:4px 8px;line-height:12px}
.main{position:absolute;top:410px;left:28px;width:548px}
.listing{background:#fff;margin-bottom:14px;box-shadow:0 1px 3px rgba(0,0,0,.25);height:224px}
.listing-title{background:linear-gradient(#4a4a4a,#222);color:#fff;font-size:10px;font-weight:700;padding:0 12px;line-height:26px;border-radius:3px 3px 0 0}
.listing-body{display:flex;padding:14px 12px}
.listing-media{width:140px;flex:none}
.coins{display:flex;gap:8px}
.coin{width:52px;height:52px;border-radius:50%;background:radial-gradient(#d9b45a,#8a6a22)}
.details-btn{margin-top:12px;display:inline-block;background:var(--red);color:#fff;font-size:9px;font-weight:700;padding:4px 14px;border-radius:3px}
.listing-info{font-size:9px;line-height:12px;color:var(--text)}
.listing-info h3{font-size:10px;line-height:13px;margin-bottom:6px}
.listing-info .label{color:var(--red);font-weight:700;font-size:10px;margin-top:6px}
.listing-info .addr{margin-top:6px}
.sidebar{position:absolute;top:408px;left:590px;width:222px}
.widget-title{font-family:"Oswald",sans-serif;font-size:17px;color:var(--dark);margin-bottom:8px}
.featured{background:#fff;padding:8px;box-shadow:0 1px 3px rgba(0,0,0,.2);height:186px;font-size:8px;line-height:11px}
.featured .cat{color:var(--navy);font-weight:700;margin-bottom:4px}
.featured-row{display:flex;gap:8px}
.car{width:98px;height:70px;flex:none;background:linear-gradient(#b9c3cc,#6c7680)}
.video{margin-top:14px;height:168px;background:#111;position:relative}
.video-still{position:absolute;inset:8px 8px 24px 8px;background:linear-gradient(120deg,#5a1a1a,#9a3a2a 50%,#2c2c3c)}
.video-bar{position:absolute;left:8px;right:8px;bottom:6px;height:10px;background:#333}
.signup{margin-top:14px;background:var(--dark);padding:10px;height:126px}
.signup .widget-title{color:#fff}
.signup-input{background:#fff;height:20px;font-size:8px;color:var(--muted);padding:0 6px;line-height:20px}
.subscribe{margin-top:10px;display:inline-block;background:var(--red);color:#fff;font-size:10px;padding:4px 14px;border-radius:3px}
.testimonials{margin-top:14px}
.testimonials p{font-size:9px;line-height:12px;color:var(--text);padding:0 4px}
.testimonials .by{text-align:right;color:var(--red);font-style:italic;margin-top:6px}
.footer{position:absolute;top:1142px;left:0;width:841px;height:58px;background:linear-gradient(#3a3a3a,#151515);color:#ddd;font-size:8px;padding:8px 28px;line-height:12px}
.badges{position:absolute;right:28px;top:10px;display:flex;gap:8px}
.badge{width:70px;height:34px;background:#f0f0f0;border-radius:2px}
</style>
</head>
<body>
<header class="header">
  <div class="brand-mark"></div>
  <div class="brand-name">BROOKHOLLOW</div>
</header>
<nav class="nav">
  <a class="active">Home</a><a>Upcoming Auctions</a><a>Auction Results</a><a>Sell or Consign</a><a>About Us</a><a>Services</a><a>FAQ</a><a>Contact Us</a>
</nav>
<div class="slideshow" role="img" aria-label="Slideshow photo of rare coins displayed in trays">
  <div class="slide-tab">News Debate<br>Testimonials</div>
</div>

<main class="main">
  <article class="listing">
    <div class="listing-title">RIDGEWAY PHYSICAL THERAPY IN MAPLE FALLS, GA</div>
    <div class="listing-body">
      <div class="listing-media">
        <div class="coins" role="img" aria-label="Coins for auction"><div class="coin"></div><div class="coin"></div></div>
        <span class="details-btn">Details</span>
      </div>
      <div class="listing-info">
        <h3>Dale Harmon Auctions, LLC GAL 9163 - Everything sold to the high bidder</h3>
        <div>Location:</div><div>Location 1 - 412 Orchard Hwy</div><div>Location 2 - 19 Cedar Bend # 2</div><div>Maple Falls, GA 30977</div>
        <div class="label">Location</div>
        <div>Begins: Friday, May 24, 2013 at 10:00 AM EDT</div><div>Ends: Wednesday, June 05, 2013 at 10:00 AM EDT</div>
        <div class="addr">88 Fenwick Ln. NW</div><div>Lowell Springs, IA 52880</div>
      </div>
    </div>
  </article>
  <article class="listing">
    <div class="listing-title">RIDGEWAY PHYSICAL THERAPY IN MAPLE FALLS, GA</div>
    <div class="listing-body">
      <div class="listing-media">
        <div class="coins" role="img" aria-label="Coins for auction"><div class="coin"></div><div class="coin"></div></div>
        <span class="details-btn">Details</span>
      </div>
      <div class="listing-info">
        <h3>Dale Harmon Auctions, LLC GAL 9163 - Everything sold to the high bidder</h3>
        <div>Location:</div><div>Location 1 - 412 Orchard Hwy</div><div>Location 2 - 19 Cedar Bend # 2</div><div>Maple Falls, GA 30977</div>
        <div class="label">Location</div>
        <div>Begins: Friday, May 24, 2013 at 10:00 AM EDT</div><div>Ends: Wednesday, June 05, 2013 at 10:00 AM EDT</div>
        <div class="addr">88 Fenwick Ln. NW</div><div>Lowell Springs, IA 52880</div>
      </div>
    </div>
  </article>
  <article class="listing">
    <div class="listing-title">RIDGEWAY PHYSICAL THERAPY IN MAPLE FALLS, GA</div>
    <div class="listing-body">
      <div class="listing-media">
        <div class="coins" role="img" aria-label="Coins for auction"><div class="coin"></div><div class="coin"></div></div>
        <span class="details-btn">Details</span>
      </div>
      <div class="listing-info">
        <h3>Dale Harmon Auctions, LLC GAL 9163 - Everything sold to the high bidder</h3>
        <div>Location:</div><div>Location 1 - 412 Orchard Hwy</div><div>Location 2 - 19 Cedar Bend # 2</div><div>Maple Falls, GA 30977</div>
        <div class="label">Location</div>
        <div>Begins: Friday, May 24, 2013 at 10:00 AM EDT</div><div>Ends: Wednesday, June 05, 2013 at 10:00 AM EDT</div>
        <div class="addr">88 Fenwick Ln. NW</div><div>Lowell Springs, IA 52880</div>
      </div>
    </div>
  </article>
</main>

<aside class="sidebar">
  <section>
    <h2 class="widget-title">Featured Auction</h2>
    <div class="featured">
      <div class="cat">AUTOMOBILES, MULTI-LOT</div>
      <div class="featured-row">
        <div class="car" role="img" aria-label="Photo of a featured automobile"></div>
        <div>07/19/13 at 12:00 PM EDT<br>P.O. Box 4418<br>Millbrook, VA 24688<br><br>Vehicles and trucks offered, full listing inside.</div>
      </div>
    </div>
  </section>
  <section class="video">
    <div class="video-still" role="img" aria-label="Video still of an auctioneer speaking"></div>
    <div class="video-bar"></div>
  </section>
  <section class="signup">
    <h2 class="widget-title">Email sign up</h2>
    <div class="signup-input">Enter Your Email Address</div>
    <span class="subscribe">Subscribe</span>
  </section>
  <section class="testimonials">
    <h2 class="widget-title">Client Testimonials</h2>
    <p>“Simply dummy text of the printing and typesetting industry. Lorem Ipsum has been the industry's best a galley of type and scrambled dummy text ever since the 1500s, when an unknown printer took a galley of type and scrambled it to make a book a galley of type and scrambled.”</p>
    <p class="by">By Alan Porter</p>
  </section>
</aside>

<footer class="footer">
  <div>Phone: 555-470-2017, Email: info@brookhollowauctions.example</div>
  <div>Copyright (c) BROOKHOLLOW 2013 - 2014 . All Rights Reserved</div>
  <div class="badges"><div class="badge"></div><div class="badge"></div></div>
</footer>
</body>
</html>
```